Interior designer needs a power point template design

I need a template PowerPoint design for my client presentations. The presentations I prepare for my clients usually include the furniture project, the detail of the selected furniture, and the costs. There are a lot of images I insert. What I need is to have a template that I can use for all my presentations, where from time to time I will insert the specific images and descriptions I want to insert. What will always be the same will be the cover, the colors, the font, and the design of the internal sections.
I already have my logo that I would like to insert on each page of the presentation (in small size).
In summary, I need:
- basic template design
- cover with an image chosen by Pictavale photo
- design an internal section/chapter
- internal page design.

I like the clolors of pink and brown <8please see image attached)
Images (will come from Pictavale photo)
● entrance/hall
● living room
● dining room
● Bathroom
● Closet
● Kids room
● Master bedroom
● Master bathroom
● Kitchen
● Office
● Laundry
● Balcony or Terrace

Target Market(s)

Customers (both residential and commercial projects)

Industry/Entity Type

interior design

Font styles to use
Other font styles liked:
• I like courier new

Requirements
Must have
• beautiful design
Should not have
• animations

```html
<!DOCTYPE html>
<html lang="it">
<head>
<meta charset="utf-8">
<title>Camera padronale – Interior Design template</title>
<link rel="stylesheet" href="https://fonts.googleapis.com/css2?family=Lora:wght@500&family=Courier+Prime&display=swap">
<style>
  :root {
    --board: #4a4a4a;
    --blush: #f2dcdc;
    --clay: #c68b78;
    --maroon: #6b1f1f;
    --white: #ffffff;
    --serif: "Lora", Georgia, serif;
    --mono: "Courier Prime", "Courier New", monospace;
  }
  * { box-sizing: border-box; margin: 0; padding: 0; }
  html, body { width: 1200px; height: 1200px; overflow: hidden; background: var(--board); }
  .canvas { position: relative; width: 1200px; height: 1200px; }

  .slide { position: absolute; background: var(--blush); overflow: hidden; }
  .slide > * { position: absolute; }
  .slide--small { width: 375px; height: 211px; }
  .block { background: var(--clay); }
  .photo { display: block; }

  .title { font-family: var(--serif); font-weight: 500; color: var(--maroon); font-size: 32px; line-height: 1.14; letter-spacing: -0.2px; white-space: nowrap; }
  .kicker { font-family: var(--mono); color: var(--clay); font-size: 10px; letter-spacing: 0.3px; }
  .caption { font-family: var(--mono); color: var(--maroon); font-size: 9.5px; line-height: 1.2; white-space: nowrap; }
  .caption--center { text-align: center; }
  .block .caption { color: var(--white); position: absolute; left: 0; right: 0; text-align: center; top: 50%; transform: translateY(-50%); }

  .brand { background: var(--white); display: flex; flex-direction: column; align-items: center; justify-content: center; gap: 3px; }
  .brand__dot { border: 1px solid var(--maroon); border-radius: 50%; }
  .brand__name { font-family: var(--serif); font-weight: 500; color: var(--maroon); text-align: center; line-height: 1; }
  .brand--small { right: 1px; top: 0; width: 34px; height: 47px; }
  .brand--small .brand__dot { width: 18px; height: 18px; }
  .brand--small .brand__name { font-size: 6px; }

  /* cover */
  .cover { left: 196px; top: 32px; width: 808px; height: 455px; }
  .cover .title { font-size: 68px; line-height: 1.15; left: 405px; top: 102px; }
  .cover__rule { left: 409px; top: 274px; width: 199px; height: 3px; background: var(--maroon); }
  .cover__label { left: 413px; top: 296px; font-family: var(--mono); color: var(--maroon); font-size: 20px; }
  .cover .brand { left: 734px; top: 0; width: 74px; height: 103px; }
  .cover .brand__dot { width: 40px; height: 40px; }
  .cover .brand__name { font-size: 11px; }

  .contact { font-family: var(--mono); color: var(--maroon); font-size: 9.5px; line-height: 1.2; }
  .contact a { color: #2a3bd6; }
</style>
</head>
<body>
<main class="canvas">

  <!-- Cover -->
  <section class="slide cover">
    <div class="block" style="left:0;top:0;width:334px;height:455px"></div>
    <svg class="photo" style="left:45px;top:43px" width="337" height="367" role="img" aria-label="Illustrazione di una camera da letto con persona che dorme">
      <defs><linearGradient id="cov" x1="0" y1="0" x2="0" y2="1"><stop offset="0" stop-color="#fbe6cf"/><stop offset="0.6" stop-color="#f3d2b4"/><stop offset="1" stop-color="#e9c79b"/></linearGradient></defs>
      <rect width="337" height="367" fill="url(#cov)"/>
    </svg>
    <h1 class="title">Camera<br>padronale</h1>
    <div class="cover__rule"></div>
    <p class="cover__label">Interior Design</p>
    <div class="block" style="left:754px;top:323px;width:54px;height:132px"></div>
    <div class="block" style="left:674px;top:402px;width:134px;height:53px"></div>
    <div class="brand"><span class="brand__dot"></span><span class="brand__name">CASA<br>LIEVE</span></div>
  </section>

  <!-- Section: Camera padronale -->
  <section class="slide slide--small" style="left:23px;top:510px">
    <div class="block" style="left:0;top:103px;width:375px;height:108px"></div>
    <h2 class="title" style="left:24px;top:22px">Camera<br>padronale</h2>
    <p class="caption" style="left:24px;top:136px">L’arredamento<br>della camera padronale</p>
    <svg class="photo" style="left:193px;top:33px" width="135" height="144" role="img" aria-label="Render della camera padronale"><rect width="135" height="144" fill="#8a8a8c"/></svg>
    <div class="brand brand--small"><span class="brand__dot"></span><span class="brand__name">CASA LIEVE</span></div>
  </section>

  <!-- Internal: Camera padronale -->
  <section class="slide slide--small" style="left:412px;top:513px">
    <svg class="photo" style="left:20px;top:30px" width="127" height="181" role="img" aria-label="Render del letto matrimoniale"><rect width="127" height="181" fill="#9a9a9e"/></svg>
    <div class="block" style="left:147px;top:30px;width:11px;height:62px"></div>
    <p class="kicker" style="left:177px;top:50px">Interior</p>
    <h2 class="title" style="left:176px;top:62px">Camera<br>padronale</h2>
    <p class="caption" style="left:183px;top:156px">L’arredamento<br>della camera padronale</p>
    <div class="block" style="left:350px;top:148px;width:25px;height:63px"></div>
    <div class="brand brand--small"><span class="brand__dot"></span><span class="brand__name">CASA LIEVE</span></div>
  </section>

  <!-- Section: Camera Armadio -->
  <section class="slide slide--small" style="left:801px;top:513px">
    <div class="block" style="left:0;top:67px;width:375px;height:92px"></div>
    <svg class="photo" style="left:40px;top:57px" width="142" height="118" role="img" aria-label="Illustrazione di uno stender con abiti"><rect width="142" height="118" fill="#efe2da"/></svg>
    <p class="kicker" style="left:200px;top:50px">Interior</p>
    <h2 class="title" style="left:200px;top:75px">Camera<br>Armadio</h2>
    <p class="caption" style="left:207px;top:172px">L’arredamento<br>della camera padronale</p>
    <div class="brand brand--small"><span class="brand__dot"></span><span class="brand__name">CASA LIEVE</span></div>
  </section>

  <!-- Internal: Camera Armadio -->
  <section class="slide slide--small" style="left:23px;top:735px">
    <div class="block" style="left:61px;top:87px;width:131px;height:70px"></div>
    <svg class="photo" style="left:35px;top:25px" width="138" height="117" role="img" aria-label="Render della cabina armadio"><rect width="138" height="117" fill="#6e6e70"/></svg>
    <p class="kicker" style="left:211px;top:60px">Interior</p>
    <h2 class="title" style="left:210px;top:72px">Camera<br>Armadio</h2>
    <p class="caption" style="left:38px;top:174px">L’arredamento<br>della camera padronale</p>
    <p class="caption" style="left:210px;top:162px">L’arredamento<br>della camera padronale</p>
    <div class="block" style="left:348px;top:182px;width:27px;height:29px"></div>
    <div class="brand brand--small"><span class="brand__dot"></span><span class="brand__name">CASA LIEVE</span></div>
  </section>

  <!-- Internal: Camera Armadio, dettaglio -->
  <section class="slide slide--small" style="left:412px;top:735px">
    <div class="block" style="left:0;top:0;width:117px;height:211px"></div>
    <svg class="photo" style="left:40px;top:32px" width="136" height="146" role="img" aria-label="Render di scarpiera e appendiabiti"><rect width="136" height="146" fill="#4d4d52"/></svg>
    <p class="kicker" style="left:204px;top:60px">Interior</p>
    <h2 class="title" style="left:204px;top:72px">Camera<br>Armadio</h2>
    <p class="caption" style="left:204px;top:154px">L’arredamento<br>della camera padronale</p>
    <div class="block" style="left:314px;top:189px;width:61px;height:22px"></div>
    <div class="brand brand--small"><span class="brand__dot"></span><span class="brand__name">CASA LIEVE</span></div>
  </section>

  <!-- Section: Bagno padronale -->
  <section class="slide slide--small" style="left:801px;top:735px">
    <div class="block" style="left:0;top:0;width:375px;height:92px"></div>
    <h2 class="title" style="left:36px;top:48px">Bagno<br>padronale</h2>
    <p class="caption" style="left:41px;top:142px">L’arredamento<br>della cabina armadio</p>
    <svg class="photo" style="left:197px;top:37px" width="136" height="122" role="img" aria-label="Illustrazione di un bagno con vasca"><rect width="136" height="122" fill="#eef3f2"/></svg>
    <p class="caption caption--center" style="left:205px;top:174px;width:120px">L’arredamento<br>della cabina armadio</p>
    <div class="brand brand--small"><span class="brand__dot"></span><span class="brand__name">CASA LIEVE</span></div>
  </section>

  <!-- Internal: Bagno padronale -->
  <section class="slide slide--small" style="left:23px;top:963px">
    <div class="block" style="left:0;top:0;width:37px;height:34px"></div>
    <h2 class="title" style="left:24px;top:58px">Bagno<br>padronale</h2>
    <p class="caption" style="left:29px;top:156px">L’arredamento<br>della cabina armadio</p>
    <svg class="photo" style="left:181px;top:0" width="106" height="211" role="img" aria-label="Render del bagno con vasca freestanding"><rect width="106" height="211" fill="#5a5d63"/></svg>
    <div class="block" style="left:280px;top:88px;width:95px;height:68px"><p class="caption">L’arredamento<br>della cabina<br>armadio</p></div>
    <div class="brand brand--small"><span class="brand__dot"></span><span class="brand__name">CASA LIEVE</span></div>
  </section>

  <!-- Internal: Bagno padronale, griglia -->
  <section class="slide slide--small" style="left:412px;top:963px">
    <svg class="photo" style="left:0;top:0" width="106" height="104" role="img" aria-label="Render del lavabo"><rect width="106" height="104" fill="#7c7e82"/></svg>
    <div class="block" style="left:106px;top:0;width:105px;height:104px"><p class="caption">L’arredamento<br>della cabina<br>armadio</p></div>
    <div class="block" style="left:0;top:104px;width:106px;height:107px"><p class="caption">L’arredamento<br>della cabina<br>armadio</p></div>
    <svg class="photo" style="left:106px;top:104px" width="105" height="107" role="img" aria-label="Render della vasca"><rect width="105" height="107" fill="#66696e"/></svg>
    <h2 class="title" style="left:222px;top:62px">Bagno<br>padronale</h2>
    <p class="caption" style="left:228px;top:164px">L’arredamento<br>della cabina armadio</p>
    <div class="brand brand--small"><span class="brand__dot"></span><span class="brand__name">CASA LIEVE</span></div>
  </section>

  <!-- Closing: contatti -->
  <section class="slide slide--small" style="left:801px;top:963px">
    <div class="block" style="left:0;top:0;width:105px;height:211px"></div>
    <div class="block" style="left:347px;top:0;width:28px;height:50px"></div>
    <div class="brand" style="left:53px;top:35px;width:99px;height:140px;gap:10px"><span class="brand__dot" style="width:54px;height:54px"></span><span class="brand__name" style="font-size:14px">CASA<br>LIEVE</span></div>
    <h2 class="title" style="left:177px;top:35px">Casa<br>Lieve</h2>
    <p class="contact" style="left:182px;top:131px">di Marta Coladi<br>via dei Tigli, 24<br><a href="mailto:marta.coladi@example.com">marta.coladi@example.com</a></p>
    <p class="contact" style="left:182px;top:175px">340/5518263</p>
  </section>

</main>
</body>
</html>
```